Satchel & Sundial needs new business card design

I need a new business card design. I'm looking for out-of-the-box design which represents the freedom of being a location independent entrepreneur.
I offer coaching, retreats and trips.
I would like to see designs with and without the photo.
Colors I use are black (#000000), green (#25A796) and brown (#D7C38C)
Website satchelandsundial.example

Target Market(s)

location independent entrepreneurs, digital nomads, people looking to swap the 9 to 5 for a lifestyle business

Industry/Entity Type

Business

Contact Information for Business Card

Dorota Falkner
Your Lifestyle Business Coach, Retreat & Trip Leader
http://satchelandsundial.example
hello@satchelandsundial.example
Live a life you don't need a holiday from

Font styles to use
Serif
Sans Serif

Requirements
Must have
• One side should contain only the logo. I would also consider having the "Live a life you don't need a holiday from" on that side too (depending on how it looks)
• Please show both sides on the designs.

```html
<!DOCTYPE html>
<html lang="en">
<head>
<meta charset="utf-8">
<title>Satchel &amp; Sundial – Business Card</title>
<link rel="stylesheet" href="https://fonts.googleapis.com/css2?family=Oswald:wght@400;500;600&family=Caveat:wght@500&display=swap">
<style>
  :root {
    --black: #1a1a1a;
    --green: #25a796;
    --brown: #d7c38c;
    --white: #ffffff;
    --backdrop: #e4e4e4;
    --card-edge: #d6d6d6;
  }
  * { box-sizing: border-box; margin: 0; padding: 0; }
  html, body {
    width: 1200px;
    height: 576px;
    overflow: hidden;
    background: var(--backdrop);
    font-family: "Oswald", sans-serif;
  }
  .canvas {
    position: relative;
    width: 1200px;
    height: 576px;
  }
  .card {
    position: absolute;
    top: 139px;
    width: 482px;
    height: 292px;
    background: var(--white);
    border: 1px solid var(--card-edge);
    border-radius: 8px;
    overflow: hidden;
  }
  .card--front { left: 82px; }
  .card--back { left: 602px; }

  .brand-name {
    font-family: "Oswald", sans-serif;
    font-weight: 500;
    font-size: 36px;
    letter-spacing: 1px;
    color: var(--black);
    text-transform: uppercase;
    white-space: nowrap;
    line-height: 1;
  }
  .card--front .brand-name {
    position: absolute;
    left: 0;
    right: 0;
    top: 104px;
    text-align: center;
  }
  .card--back .brand-name {
    position: absolute;
    left: 20px;
    top: 100px;
  }

  .wave {
    position: absolute;
    left: 0;
    top: 0;
    width: 482px;
    height: 292px;
  }
  .wave__shade { fill: var(--black); }
  .wave__brown { fill: none; stroke: var(--brown); stroke-width: 7; stroke-linecap: round; }
  .wave__green { fill: none; stroke: var(--green); stroke-width: 5; }

  .holder {
    position: absolute;
    right: 22px;
    top: 26px;
    text-align: right;
  }
  .holder__name {
    font-weight: 600;
    font-size: 20px;
    letter-spacing: 0.3px;
    color: var(--brown);
    text-transform: uppercase;
    line-height: 1.1;
  }
  .holder__role {
    font-weight: 400;
    font-size: 11.5px;
    color: var(--white);
    line-height: 1.45;
    margin-top: 4px;
  }

  .contacts {
    position: absolute;
    left: 22px;
    top: 208px;
    list-style: none;
  }
  .contacts__item {
    display: flex;
    align-items: center;
    height: 20.5px;
    font-size: 12.5px;
    color: var(--black);
  }
  .contacts__icon {
    width: 12px;
    height: 12px;
    margin-right: 9px;
    flex: none;
  }
  .contacts__social {
    width: 10px;
    height: 10px;
    background: var(--black);
    border-radius: 2px;
    margin-right: 11px;
    margin-left: 1px;
    flex: none;
  }
  .accent { color: var(--green); }

  .motto {
    position: absolute;
    right: 22px;
    top: 224px;
    text-align: right;
    font-family: "Caveat", cursive;
    font-weight: 500;
    font-size: 19px;
    line-height: 1.35;
    color: var(--green);
  }
</style>
</head>
<body>
<main class="canvas">

  <section class="card card--front" aria-label="Card front">
    <p class="brand-name">Satchel &amp; Sundial</p>
  </section>

  <section class="card card--back" aria-label="Card back">
    <svg class="wave" viewBox="0 0 482 292" aria-hidden="true">
      <path class="wave__shade" d="M0,0 H482 V133 C400,134 330,92 250,58 C180,30 90,18 0,34 Z"/>
      <path class="wave__brown" d="M2,44 C80,24 190,22 290,52"/>
      <path class="wave__green" d="M58,54 C150,34 240,58 320,96 C380,126 430,142 482,144"/>
    </svg>

    <div class="holder">
      <p class="holder__name">Dorota Falkner</p>
      <p class="holder__role">Your Lifestyle Business Coach<br>Retreat &amp; Trip Leader</p>
    </div>

    <p class="brand-name">Satchel &amp; Sundial</p>

    <ul class="contacts">
      <li class="contacts__item">
        <svg class="contacts__icon" viewBox="0 0 12 12" aria-hidden="true">
          <rect x="0.5" y="2" width="11" height="8" fill="var(--green)"/>
          <path d="M0.5,2 L6,6.5 L11.5,2" fill="none" stroke="var(--white)" stroke-width="1"/>
        </svg>
        hello@satchelandsundial.example
      </li>
      <li class="contacts__item">
        <svg class="contacts__icon" viewBox="0 0 12 12" aria-hidden="true">
          <circle cx="6" cy="6" r="5.2" fill="none" stroke="var(--green)" stroke-width="1.2"/>
          <ellipse cx="6" cy="6" rx="2.2" ry="5.2" fill="none" stroke="var(--green)" stroke-width="1"/>
          <line x1="0.8" y1="6" x2="11.2" y2="6" stroke="var(--green)" stroke-width="1"/>
        </svg>
        <span>www.<span class="accent">satchelandsundial</span>.example</span>
      </li>
      <li class="contacts__item">
        <span class="contacts__social" aria-hidden="true"></span>
        <span class="accent">/satchelandsundial</span>
      </li>
    </ul>

    <p class="motto">Live a life you<br>dont need a holiday from</p>
  </section>

</main>
</body>
</html>
```